Birchline Septic Solutions

Would like to see some single sided ones but would also like to see some double sided with one sided only being the logo. Owners name is Colin Vandro. Phone number is 555-214-0387
Services are pumping, inspections, installs, and repairs

Contact Information for Business Card

555-241-0387 Colin Vandro Fairbrook, OH

```html
<!DOCTYPE html>
<html lang="en">
<head>
<meta charset="utf-8">
<title>Birchline Septic Solutions – Business Card</title>
<link rel="stylesheet" href="https://fonts.googleapis.com/css2?family=Montserrat:wght@400;500;800&display=swap">
<style>
  :root {
    --backdrop: #3b3b3b;
    --card-white: #ffffff;
    --card-black: #141414;
    --ink: #111111;
    --muted: #555555;
    --teal: #2bb7b0;
    --divider: #7a7a7a;
  }
  * { box-sizing: border-box; margin: 0; padding: 0; }
  html, body { width: 1200px; height: 801px; overflow: hidden; }
  body {
    background: var(--backdrop);
    font-family: "Montserrat", sans-serif;
    position: relative;
  }
  .card {
    position: absolute;
    top: 252px;
    width: 520px;
    height: 297px;
    border-bottom: 3px solid var(--teal);
    box-shadow: 0 10px 30px rgba(0,0,0,.35);
    overflow: hidden;
  }
  .card--front { left: 60px; background: var(--card-white); }
  .card--back { left: 620px; background: var(--card-black); }

  /* front */
  .brand {
    position: absolute;
    left: 30px; top: 104px;
    width: 220px;
    color: var(--ink);
    font-weight: 800;
    text-align: center;
  }
  .brand__name { font-size: 40px; line-height: 1; letter-spacing: 0.5px; }
  .brand__tag { font-size: 12px; letter-spacing: 4px; margin-top: 10px; font-weight: 800; }
  .divider {
    position: absolute;
    left: 266px; top: 70px;
    width: 1px; height: 150px;
    background: var(--divider);
  }
  .contact {
    position: absolute;
    left: 284px; top: 78px;
    width: 226px;
    color: var(--muted);
  }
  .contact__name { font-size: 17px; font-weight: 800; color: var(--ink); }
  .contact__role { font-size: 13px; color: var(--teal); margin-top: 2px; font-weight: 500; }
  .contact__list { list-style: none; margin-top: 16px; }
  .contact__item {
    display: flex; align-items: center; gap: 7px;
    font-size: 11px; line-height: 20px;
    white-space: nowrap;
  }
  .contact__icon { width: 10px; height: 10px; fill: var(--teal); flex: none; }

  /* back */
  .back-pattern {
    position: absolute; inset: 0;
    background: linear-gradient(135deg, #1c1c1c 0%, #0e0e0e 45%, #262626 100%);
  }
  .back-brand {
    position: absolute;
    right: 70px; bottom: 70px;
    color: #ffffff;
    font-size: 30px;
    font-weight: 800;
    letter-spacing: 0.5px;
  }
</style>
</head>
<body>

<section class="card card--front" aria-label="Business card front">
  <div class="brand">
    <div class="brand__name">Birchline</div>
    <div class="brand__tag">SEPTIC SOLUTIONS</div>
  </div>
  <div class="divider"></div>
  <div class="contact">
    <div class="contact__name">COLIN VANDRO</div>
    <div class="contact__role">Founder / CEO</div>
    <ul class="contact__list">
      <li class="contact__item">
        <svg class="contact__icon" viewBox="0 0 10 10"><path d="M2 0.5 L3.8 2.6 L2.9 3.8 Q4 6 6.2 7.1 L7.4 6.2 L9.5 8 L8.3 9.5 Q4.5 9.5 0.5 1.7 Z"/></svg>
        555-241-0387
      </li>
      <li class="contact__item">
        <svg class="contact__icon" viewBox="0 0 10 10"><rect x="0" y="2" width="10" height="6.5" rx="1"/><path d="M0.5 2.5 L5 6 L9.5 2.5" stroke="#fff" stroke-width="1" fill="none"/></svg>
        info@birchlinesepticsolutions.com
      </li>
      <li class="contact__item">
        <svg class="contact__icon" viewBox="0 0 10 10"><circle cx="5" cy="5" r="4.5"/><path d="M0.5 5 H9.5 M5 0.5 Q2.5 5 5 9.5 M5 0.5 Q7.5 5 5 9.5" stroke="#fff" stroke-width="0.8" fill="none"/></svg>
        www.birchlinesepticsolutions.com
      </li>
      <li class="contact__item">
        <svg class="contact__icon" viewBox="0 0 10 10"><path d="M5 0 A3.6 3.6 0 0 1 8.6 3.6 C8.6 6 5 10 5 10 C5 10 1.4 6 1.4 3.6 A3.6 3.6 0 0 1 5 0 Z"/><circle cx="5" cy="3.6" r="1.3" fill="#fff"/></svg>
        Fairbrook, OH
      </li>
    </ul>
  </div>
</section>

<section class="card card--back" aria-label="Business card back">
  <div class="back-pattern" role="img" aria-label="Repeating tone-on-tone gloss pattern of the company mark"></div>
  <div class="back-brand">Birchline</div>
</section>

</body>
</html>
```